Bloom Path! A website showcasing who I am as a person

Bloom Path started out as idea for me to better myself as a person and work on small projects that would help me grow as a person. Now I want to build a website showcasing "Bloom Path." I want the website to showcase who I am and how I have grown both professionally and personally. I can build the raw code of the website on my own but I am not really much of a designer. I am looking for a design where I can write and post blogs, articles and share my thoughts. A little about myself and the ideas and interests that I want to share
What is Bloom Path
Who I am
Background - Professional
Brand Marketing
Email Automation
Hiking
Rock Climbing
Traveling
Exercising and Transformation
"Personal Thoughts"
Hopefully this is enough information to get people started on some designs.
Work
3 page

```html
<!DOCTYPE html>
<html lang="en">
<head>
<meta charset="utf-8">
<title>Ravi Kalan — Bloom Path</title>
<link href="https://fonts.googleapis.com/css2?family=Rye&family=Roboto:wght@400;500;700&family=Open+Sans:wght@400;600;700&family=Montserrat:wght@500;600;700&display=swap" rel="stylesheet">
<style>
:root{
  --blue:#2f6db5;
  --ink:#2b2b2b;
  --text:#555;
  --line:#d9d9d9;
  --grey-band:#ececec;
  --white:#fff;
}
*{box-sizing:border-box;margin:0;padding:0}
html,body{width:1200px;height:3098px;overflow:hidden}
body{position:relative;background:var(--white);font-family:"Open Sans",sans-serif;color:var(--text)}
.abs{position:absolute}
.photo{position:absolute;overflow:hidden}

/* top bar */
.topbar{left:0;top:0;width:1200px;height:42px;background:var(--blue);color:var(--white);display:flex;align-items:center;padding:0 96px;font:600 15px "Open Sans",sans-serif}
.topbar .menu{margin-right:14px}
.topbar .social{margin-left:auto;display:flex;gap:8px}
.topbar .social span{width:19px;height:19px;border:2px solid var(--white);border-radius:50%}

/* hero */
.hero{left:0;top:42px;width:1200px;height:423px;background:linear-gradient(180deg,#8a8e84 0%,#5f6258 45%,#3d3530 75%,#2a221e 100%)}
.hero-title{left:0;top:200px;width:1200px;text-align:center;color:var(--white);font:58px "Rye",serif;letter-spacing:2px}
.hero-sub{left:0;top:283px;width:1200px;text-align:center;color:var(--white);font:700 18px "Open Sans",sans-serif;letter-spacing:.5px}

/* intro */
.intro-title{left:0;top:506px;width:1200px;text-align:center;font:500 36px "Roboto",sans-serif;color:var(--ink);letter-spacing:.5px}
.intro-text{left:165px;top:568px;width:870px;text-align:center;font:13.5px/21px "Open Sans",sans-serif;color:var(--text)}

/* about */
.about{left:83px;top:660px;width:392px;text-align:center}
.about h2{font:400 36px "Roboto",sans-serif;color:var(--ink);letter-spacing:1px}
.about .avatar{width:240px;height:240px;border-radius:50%;margin:30px auto 0;background:radial-gradient(circle at 50% 45%,#d9b49a 0%,#a77a5e 45%,#4b3a30 100%)}
.about h3{margin-top:26px;font:700 20px "Roboto",sans-serif;color:#444;letter-spacing:1px}
.about p{margin-top:18px;font:13.5px/22px "Open Sans",sans-serif;color:var(--text)}
.about .dots{margin-top:24px;display:flex;justify-content:center;gap:24px}
.about .dots span{width:12px;height:12px;border-radius:50%;background:#333}
.divider{left:494px;top:660px;height:497px;border-left:2px dashed #999}

/* featured slide */
.feature-img{left:531px;top:665px;width:567px;height:273px;border-radius:4px;background:linear-gradient(160deg,#8a8275 0%,#5b5a63 45%,#2e3a5a 75%,#1d2236 100%)}
.feature-img .cap{position:absolute;right:32px;top:153px;color:var(--white);font:700 30px "Roboto",sans-serif}
.feature-img .cap-text{position:absolute;left:32px;right:32px;top:205px;color:var(--white);font:700 13px/22px "Open Sans",sans-serif;text-align:right}
.feature-title{left:531px;top:955px;font:700 24px "Roboto",sans-serif;color:var(--ink)}
.feature-text{left:531px;top:996px;font:600 12.5px "Open Sans",sans-serif;color:#444}
.thumb{top:1033px;width:163px;height:113px}
.slider-dots{left:1030px;top:1166px;display:flex;gap:4px}
.slider-dots span{width:13px;height:11px;background:#b8bcc4}
.slider-dots span.active{background:var(--blue)}

/* topic cards */
.card{top:1235px;width:483px;height:324px}
.card .label{position:absolute;left:30px;bottom:44px;color:var(--white);font:700 24px "Montserrat",sans-serif;letter-spacing:1px}
.card .tag{position:absolute;left:30px;bottom:18px;color:var(--white);font:700 14px "Montserrat",sans-serif;display:flex;align-items:center;gap:6px}
.card .tag i{width:13px;height:13px;border:2px solid var(--white);border-radius:50%}
.card .heart{position:absolute;right:22px;bottom:20px}

/* tabs */
.tabs{left:97px;top:1596px;display:flex;gap:8px}
.tabs span{height:35px;padding:0 24px;display:flex;align-items:center;background:#e8e8e8;font:600 13px "Open Sans",sans-serif;color:#555}
.tabs span.active{background:var(--blue);color:var(--white)}

/* posts */
.post{left:97px;width:523px}
.post h2{font:700 27px "Roboto",sans-serif;color:var(--ink);line-height:34px}
.post .by{margin-top:4px;font:600 20px "Montserrat",sans-serif;color:#888}
.post .by b{color:var(--blue);font-weight:600}
.post .meta{margin-top:14px;padding-bottom:8px;border-bottom:1px solid var(--line);display:flex;align-items:center;font:11px "Open Sans",sans-serif;color:#666;white-space:nowrap}
.post .meta .item{display:flex;align-items:center;gap:8px;margin-right:44px}
.post .meta .share{margin-left:auto;display:flex;gap:16px}
.post .meta .share i{width:9px;height:9px;border-radius:50%;background:#999}
.post .img{width:523px;height:206px;margin-top:26px}
.post p{margin-top:20px;font:11px/21px "Open Sans",sans-serif;color:#555}
.post .more{margin-top:18px;display:inline-block;border:1.5px solid var(--blue);color:var(--blue);padding:4px 10px;font:600 11.5px "Open Sans",sans-serif;letter-spacing:.5px}

/* sidebar */
.side{left:785px;width:320px}
.side h4{font:400 17px "Roboto",sans-serif;color:#444;padding-bottom:10px;border-bottom:1.5px solid #999}
.side ul{list-style:none;margin-top:12px}
.side li{position:relative;padding-left:14px;font:11.5px/17px "Open Sans",sans-serif;color:#444;margin-bottom:12px}
.side li::before{content:"";position:absolute;left:0;top:5px;border-left:6px solid #444;border-top:4px solid transparent;border-bottom:4px solid transparent}
.side .read{font:12px "Open Sans",sans-serif;color:var(--blue)}
.ebook{left:745px;top:2478px;width:353px;height:174px;background:var(--blue);color:var(--white);text-align:center;padding-top:22px}
.ebook h3{font:600 28px "Montserrat",sans-serif;letter-spacing:.5px}
.ebook p{margin-top:14px;font:700 18px/23px "Montserrat",sans-serif}
.ebook .dots{margin-top:14px;display:flex;justify-content:center;gap:16px}
.ebook .dots span{width:9px;height:9px;border-radius:50%;background:var(--white)}

/* bottom topics */
.topic{top:2730px;width:400px;height:328px}
.topic .head{height:95px;background:var(--grey-band);text-align:center;padding-top:20px;border-right:1px solid #d5d5d5;position:relative;white-space:nowrap}
.topic .head h3{font:500 19px "Montserrat",sans-serif;color:#222;letter-spacing:.3px}
.topic .head p{margin-top:12px;font:500 13.5px "Montserrat",sans-serif;color:#444}
.topic .head::after{content:"";position:absolute;left:50%;bottom:-12px;margin-left:-12px;border-top:12px solid var(--grey-band);border-left:12px solid transparent;border-right:12px solid transparent;z-index:2}
.topic .pic{position:relative;height:233px}

.footer{left:0;top:3058px;width:1200px;height:40px;background:var(--blue);color:var(--white);text-align:center;font:600 12.5px/40px "Open Sans",sans-serif}
</style>
</head>
<body>

<header class="abs topbar">
  <svg class="menu" width="14" height="12" viewBox="0 0 14 12"><rect width="14" height="2" fill="#fff"/><rect y="5" width="14" height="2" fill="#fff"/><rect y="10" width="14" height="2" fill="#fff"/></svg>
  Welcome To Ravi Kalan
  <div class="social"><span></span><span></span><span></span><span></span></div>
</header>

<section class="abs hero" role="img" aria-label="Hiker standing on a rocky mountain peak above misty valleys"></section>
<h1 class="abs hero-title">Ravi Kalan</h1>
<p class="abs hero-sub">Personal Thoughts. Innovation. Easy To Get</p>

<h2 class="abs intro-title">Exercising And Transformation</h2>
<p class="abs intro-text">Lorem Ipsum has been the industry's standard dummy text ever since the 1500s, when an unknown printer took a galley of type and scrambled it to make a type specimen book. It has survived not only five centuries.Lorem Ipsum has been the industry's standard dummy text ever since the 1500s, when an unknown printer took a galley of type and scrambled it to make a type specimen book.</p>

<aside class="abs about">
  <h2>Bloom Path</h2>
  <div class="avatar" role="img" aria-label="Portrait photo of the author"></div>
  <h3>Ravi Kalan</h3>
  <p>Lorem Ipsum has been the industry's standard dummy text ever since the 1500s, when an unknown printer took a galley of type and scrambled it to make a type specimen book. It has survived not only five centuries</p>
  <div class="dots"><span></span><span></span><span></span><span></span></div>
</aside>
<div class="abs divider"></div>

<div class="photo feature-img" role="img" aria-label="Traveller resting with backpack in a station hall">
  <div class="cap">Traveling</div>
  <div class="cap-text">Lorem Ipsum has been the industry's standard dummy text ever since.Lorem Ipsum has been the industry's standard dummy text ever since.</div>
</div>
<h3 class="abs feature-title">Strategies for More Efficient Business Travel</h3>
<p class="abs feature-text">Lorem Ipsum has been the industry's standard dummy.Lorem Ipsum has been the industry.</p>
<div class="photo thumb" style="left:531px;background:linear-gradient(135deg,#27c3c8,#14a7b3)" role="img" aria-label="Email marketing illustration on teal background"></div>
<div class="photo thumb" style="left:733px;background:linear-gradient(135deg,#6a5646,#2f2824)" role="img" aria-label="Hands typing on a laptop"></div>
<div class="photo thumb" style="left:935px;background:linear-gradient(135deg,#eef0f4,#b9bfca)" role="img" aria-label="Businessman in white shirt"></div>
<div class="abs slider-dots"><span class="active"></span><span></span><span></span><span></span></div>

<div class="photo card" style="left:101px;background:linear-gradient(180deg,#c07a1c 0%,#e0a03e 40%,#8a5320 75%,#3a2412 100%)" role="img" aria-label="Person meditating at sunset">
  <div class="label">PERSONAL THOUGHTS</div>
  <div class="tag"><i></i>PERSONAL THOUGHTS</div>
  <svg class="heart" width="20" height="18" viewBox="0 0 20 18"><path d="M10 17 1.8 9A5 5 0 0 1 10 3a5 5 0 0 1 8.2 6Z" fill="#fff"/></svg>
</div>
<div class="photo card" style="left:615px;background:linear-gradient(135deg,#9a9a98 0%,#d8d6cf 45%,#efece3 100%)" role="img" aria-label="Hand pointing at a marketing plan sketch">
  <div class="label">BRAND MARKETING</div>
  <div class="tag"><i></i>MARKETING</div>
  <svg class="heart" width="20" height="18" viewBox="0 0 20 18"><path d="M10 17 1.8 9A5 5 0 0 1 10 3a5 5 0 0 1 8.2 6Z" fill="#fff"/></svg>
</div>

<nav class="abs tabs"><span class="active">NEW</span><span>Collections</span><span>Recommended</span><span>Popular</span></nav>

<article class="abs post" style="top:1672px">
  <h2>Traveling</h2>
  <div class="by">By <b>Declan</b></div>
  <div class="meta">
    <span class="item"><svg width="13" height="13" viewBox="0 0 13 13"><circle cx="6.5" cy="6.5" r="5.3" fill="none" stroke="#2f6db5" stroke-width="1.6"/><path d="M6.5 3.5v3h2.5" fill="none" stroke="#2f6db5" stroke-width="1.4"/></svg>March 15th,2017</span>
    <span class="item"><svg width="10" height="13" viewBox="0 0 10 13"><path d="M0 0h10v13L5 9 0 13Z" fill="#2f6db5"/></svg>Life Goal Development</span>
    <span class="item"><svg width="15" height="13" viewBox="0 0 15 13"><path d="M7.5 0C3.4 0 0 2.4 0 5.5c0 1.7 1 3.2 2.6 4.2L1.8 13l3.6-2.2c.7.2 1.4.2 2.1.2 4.1 0 7.5-2.4 7.5-5.5S11.6 0 7.5 0Z" fill="#2f6db5"/></svg>2 Comments</span>
    <span class="share"><i></i><i></i><i></i></span>
  </div>
  <div class="photo img" style="position:relative;background:linear-gradient(180deg,#c9c9a0 0%,#b7b98c 55%,#8f9a66 100%)" role="img" aria-label="Woman holding colourful balloons in a field"></div>
  <p>Lorem Ipsum is simply dummy text of the printing and typesetting industry. Lorem Ipsum has been the industry's standard dummy text ever since the 1500s, when an unknown printer took a galley of type and scrambled it to make a type specimen book. It has survived not only five centuries, but also the leap into electronic typesetting, remaining essentially unchanged. It was popularised in the 1960s.</p>
  <a class="more">READ MORE</a>
</article>

<article class="abs post" style="top:2200px">
  <h2>Email Automation</h2>
  <div class="by">By <b>Declan</b></div>
  <div class="meta">
    <span class="item"><svg width="13" height="13" viewBox="0 0 13 13"><circle cx="6.5" cy="6.5" r="5.3" fill="none" stroke="#2f6db5" stroke-width="1.6"/><path d="M6.5 3.5v3h2.5" fill="none" stroke="#2f6db5" stroke-width="1.4"/></svg>March 15th,2017</span>
    <span class="item"><svg width="10" height="13" viewBox="0 0 10 13"><path d="M0 0h10v13L5 9 0 13Z" fill="#2f6db5"/></svg>Life Goal Development</span>
    <span class="item"><svg width="15" height="13" viewBox="0 0 15 13"><path d="M7.5 0C3.4 0 0 2.4 0 5.5c0 1.7 1 3.2 2.6 4.2L1.8 13l3.6-2.2c.7.2 1.4.2 2.1.2 4.1 0 7.5-2.4 7.5-5.5S11.6 0 7.5 0Z" fill="#2f6db5"/></svg>2 Comments</span>
    <span class="share"><i></i><i></i><i></i></span>
  </div>
  <div class="photo img" style="position:relative;background:linear-gradient(135deg,#a86a3e 0%,#c99a72 40%,#5e6f86 75%,#3b4a5f 100%)" role="img" aria-label="Relaxed man leaning back at his laptop"></div>
  <p>Lorem Ipsum is simply dummy text of the printing and typesetting industry. Lorem Ipsum has been the industry's standard dummy text ever since the 1500s, when an unknown printer took a galley of type and scrambled it to make a type specimen book. It has survived not only five centuries, but also the leap into electronic typesetting, remaining essentially unchanged. It was popularised in the 1960s.</p>
  <a class="more">READ MORE</a>
</article>

<aside class="abs side" style="top:1613px">
  <h4>Categories</h4>
  <ul>
    <li>Background - Professional</li><li>Brand Marketing</li><li>Email Automation</li><li>Hiking</li><li>Rock Climbing</li><li>Traveling</li><li>Exercising and Transformation</li>
  </ul>
</aside>
<aside class="abs side" style="top:1902px">
  <h4>Recent Posts</h4>
  <ul>
    <li>Salary Packaging Basics: How To Manage Your Salary Package March 16, 2017</li>
    <li>Bad Work Habits That Can Cost You Your Job March 15, 2017</li>
    <li>10 Mindfulness Tips For All Employees March 13, 2017</li>
    <li>37 Motivational Workplace Quotes March 9, 201</li>
    <li>10 Mindfulness Tips For All Employees March 13, 2017</li>
  </ul>
  <div class="read">Read More.....</div>
</aside>
<aside class="abs side" style="top:2255px">
  <h4>Archives</h4>
  <ul>
    <li>February 2017</li><li>January 2017</li><li>December 2016</li><li>November 2016</li><li>October 2016</li>
  </ul>
</aside>
<div class="abs ebook">
  <h3>GET OUR EBOOK</h3>
  <p>CLICK HERE TO DOWNLOAD OUR<br>FULL EBOOOK VERSION</p>
  <div class="dots"><span></span><span></span><span></span></div>
</div>

<section class="abs topic" style="left:0">
  <div class="head"><h3>ROCK CLIMBING</h3><p>Setting Goals And Persevering</p></div>
  <div class="pic" style="background:linear-gradient(120deg,#5a3a22 0%,#a0683c 35%,#c9d3df 60%,#e8edf2 100%)" role="img" aria-label="Climber hanging from a rock overhang"></div>
</section>
<section class="abs topic" style="left:400px">
  <div class="head"><h3>BRAND MARKETING</h3><p>Make You More Persistent</p></div>
  <div class="pic" style="background:linear-gradient(90deg,#7a4e34 0%,#a8795a 40%,#d6d4cf 70%,#e4e2dd 100%)" role="img" aria-label="Bearded man pointing at a grey wall with painted lettering"></div>
</section>
<section class="abs topic" style="left:800px">
  <div class="head" style="border-right:none"><h3>EXERCISING AND TRANSFORMATION</h3><p>Simulating Trust And Closeness</p></div>
  <div class="pic" style="background:linear-gradient(180deg,#0c1630 0%,#1d3f86 50%,#0a1224 100%)" role="img" aria-label="Body transformation figures on a dark grid"></div>
</section>

<footer class="abs footer">© 2017 Fernway Studio. All Rights Reserved</footer>

</body>
</html>
```